Brookvale Estates LLC stationary for a real estate property management company.

Create stationary (letterhead, envelopes, business cards) using Brookvale Estates LLC logo as primary creative element. Stationary design needs to be horizontal, leaving as much space as possible for correspondence copy. See attached Creative Brief and past stationary files for details.

Target Market(s)

Prospective apartment residents and current residents, vendors, and government agencies.

Industry/Entity Type

Property Management

Contact Information for Business Card

Business card employee title: Property Manager. Should include address, phone, fax, email, website, slogan, and Brookvale Estates logo.

Font styles to use
Sans Serif

Colors
0592cd
000000

Requirements
Must have
• Tone should be conservative, institutional, business (i.e. banking, finance, real estate). Must include: address, phone, fax, website, and slogan (see attached Creative Brief). Should be a horizontal design, leaving as much room as possible for letter correspondence copy.
Nice to have
• Please use an Arial or Helvetica style font.
Should not have
• Letterhead layout should leave as much room as possible for copy.

```html
<!DOCTYPE html>
<html lang="en">
<head>
<meta charset="utf-8">
<title>Brookvale Estates LLC – Business Card</title>
<link href="https://fonts.googleapis.com/css2?family=Arimo:wght@400;700&display=swap" rel="stylesheet">
<style>
  :root {
    --brand-blue: #0c67a3;
    --ink: #3f3f3f;
    --rule: #2b2b2b;
    --card-white: #f6f6f6;
    --backdrop: #e4e4e4;
    --white: #ffffff;
  }
  * { margin: 0; padding: 0; box-sizing: border-box; }
  html, body { width: 1200px; height: 960px; overflow: hidden; }
  body {
    background: var(--backdrop);
    font-family: "Arimo", Arial, Helvetica, sans-serif;
    position: relative;
  }
  .card {
    position: absolute;
    width: 600px;
    height: 342px;
    box-shadow: 0 2px 6px rgba(0,0,0,0.25);
  }
  .card-front { left: 302px; top: 129px; background: var(--card-white); }
  .card-back { left: 299px; top: 489px; background: var(--brand-blue); }

  .wordmark {
    position: absolute;
    right: 30px;
    top: 186px;
    top: 58px;
    display: flex;
    align-items: center;
    gap: 10px;
    color: var(--brand-blue);
    font-weight: 700;
    font-size: 24px;
    letter-spacing: 0.5px;
    text-transform: uppercase;
  }
  .wordmark-square {
    width: 22px; height: 22px;
    background: var(--brand-blue);
  }

  .person { position: absolute; left: 28px; top: 197px; }
  .person-name {
    color: var(--brand-blue);
    font-weight: 700;
    font-size: 22px;
    letter-spacing: 0.2px;
  }
  .person-title { color: var(--ink); font-size: 15px; margin-top: 3px; }

  .divider {
    position: absolute;
    left: 28px; right: 30px; top: 250px;
    height: 1px; background: var(--rule);
  }

  .contact-list {
    position: absolute; left: 28px; top: 263px;
    list-style: none;
    color: var(--ink);
    font-size: 14px;
    line-height: 20px;
  }
  .contact-list li { display: flex; align-items: center; gap: 8px; }
  .contact-list svg { width: 13px; height: 13px; fill: var(--brand-blue); }

  .address {
    position: absolute; right: 30px; top: 263px;
    text-align: right;
    color: var(--ink);
    font-size: 14px;
    line-height: 19px;
    font-style: normal;
  }
  .address .web { letter-spacing: 0.8px; }

  .back-name {
    position: absolute; left: 0; right: 0; top: 140px;
    display: flex; justify-content: center; align-items: center; gap: 14px;
    color: var(--white);
    font-weight: 700;
    font-size: 34px;
    letter-spacing: 1px;
    text-transform: uppercase;
  }
  .back-name-circle {
    width: 30px; height: 30px; border-radius: 50%;
    background: var(--white);
  }
  .slogan {
    position: absolute; left: 0; right: 0; top: 287px;
    text-align: center;
    color: var(--white);
    font-weight: 700;
    font-size: 16px;
  }
</style>
</head>
<body>
  <section class="card card-front">
    <div class="wordmark"><span class="wordmark-square"></span>Brookvale Estates LLC</div>

    <div class="person">
      <div class="person-name">DANIEL HARLOW</div>
      <div class="person-title">Property Manager</div>
    </div>

    <div class="divider"></div>

    <ul class="contact-list">
      <li>
        <svg viewBox="0 0 24 24"><path d="M6.6 10.8a15.1 15.1 0 0 0 6.6 6.6l2.2-2.2a1 1 0 0 1 1-.25 11.4 11.4 0 0 0 3.6.57 1 1 0 0 1 1 1V20a1 1 0 0 1-1 1A17 17 0 0 1 3 4a1 1 0 0 1 1-1h3.5a1 1 0 0 1 1 1c0 1.25.2 2.46.57 3.6a1 1 0 0 1-.25 1z"/></svg>
        555-014-2287
      </li>
      <li>
        <svg viewBox="0 0 24 24"><path d="M6 2h12v6H6z"/><path d="M3 9h18v9h-3v4H6v-4H3zM8 15v5h8v-5z"/></svg>
        555-014-6630
      </li>
      <li>
        <svg viewBox="0 0 24 24"><path d="M2 5h20v14H2zm2 2v.5l8 5 8-5V7z"/></svg>
        daniel@brookvaleestates.us
      </li>
    </ul>

    <address class="address">
      2750 Alder Creek Road #B210<br>
      Fairview, CA 90417<br>
      <span class="web">www.brookvaleestates.us</span>
    </address>
  </section>

  <section class="card card-back">
    <div class="back-name"><span class="back-name-circle"></span>Brookvale Estates</div>
    <div class="slogan">Multifamily Property Management</div>
  </section>
</body>
</html>
```